Modern, traditional Catering Menu for hotel and conference centre

Modernization of Catering menu while still making this very legible and clear to all guests. Template required in Microsoft word document so that updates to menu items can be easily updated. Menu needs style relatable to hotel and conference centre in an area known for apples, farming and awe-inspiring landscape.

Target Market(s)

Conference and meeting groups,

Industry/Entity Type

Hospitality

Font styles to use
Serif
Script

Colors

Designer to choose colors to be used in the design.

Requirements
Must have
• Legible and clear headers and modern look.
• Microsoft word template to easily be able to make updates.
Nice to have
• Something unique related to apples and our logo

```html
<!DOCTYPE html>
<html lang="en">
<head>
<meta charset="utf-8">
<title>Catering Menu – Maple Ridge Inn</title>
<link href="https://fonts.googleapis.com/css2?family=Crimson+Text:wght@400;700&family=Kaushan+Script&display=swap" rel="stylesheet">
<style>
  :root {
    --backdrop: #e4e5e6;
    --cream: #f6f2ea;
    --cream-edge: #ede5d6;
    --footer-beige: #e6dac6;
    --footer-light: #f7f2ea;
    --paper-white: #ffffff;
    --ink: #2a1512;
    --accent-orange: #c8762a;
    --apple-red: #b8323a;
    --apple-deep: #8e1f2a;
    --apple-blush: #d86a5e;
    --wicker: #c99056;
    --wicker-dark: #9d6a35;
    --teal: #2f7a6f;
  }
  * { margin: 0; padding: 0; box-sizing: border-box; }
  html, body { width: 1200px; height: 1200px; overflow: hidden; }
  body { background: var(--backdrop); position: relative; font-family: "Crimson Text", Georgia, serif; color: var(--ink); }

  .menu-cover {
    position: absolute; left: 150px; top: 30px; width: 900px; height: 1140px;
    background: radial-gradient(ellipse at 50% 40%, var(--paper-white) 0%, var(--cream) 55%, var(--cream-edge) 100%);
    overflow: hidden;
  }
  .cover-photo {
    position: absolute; left: 0; top: 0; width: 900px; height: 430px;
    background:
      radial-gradient(ellipse at 85% 10%, var(--teal) 0%, transparent 30%),
      linear-gradient(180deg, var(--apple-blush) 0%, var(--apple-red) 28%, var(--apple-deep) 48%, var(--wicker) 62%, var(--wicker-dark) 80%, var(--wicker) 100%);
  }
  .torn-edge { position: absolute; left: 0; width: 900px; display: block; }
  .torn-edge.top { top: 370px; height: 80px; }
  .torn-edge.bottom { top: 870px; height: 80px; }
  .cover-footer {
    position: absolute; left: 0; top: 915px; width: 900px; height: 225px;
    background: radial-gradient(ellipse at 50% 85%, var(--footer-light) 0%, var(--footer-beige) 75%);
  }

  .title-block { position: absolute; left: 0; top: 465px; width: 900px; text-align: center; }
  .title-script {
    font-family: "Kaushan Script", cursive; font-size: 104px; line-height: 1;
    color: var(--ink); display: block; transform: translateX(-10px);
  }
  .title-serif-row { display: flex; justify-content: center; align-items: center; gap: 20px; margin-top: -14px; }
  .title-serif { font-size: 68px; font-weight: 700; line-height: 1; }
  .dot-rule { width: 128px; border-top: 3px dotted var(--accent-orange); margin-top: 34px; }

  .audience { position: absolute; left: 0; top: 692px; width: 900px; text-align: center; font-size: 29px; }
  .pricing-note { position: absolute; left: 0; top: 733px; width: 900px; text-align: center; font-size: 17px; color: var(--accent-orange); }

  .brand-row { position: absolute; left: 190px; top: 950px; display: flex; align-items: center; }
  .brand-name-mark {
    width: 100px; font-size: 22px; line-height: 1.05; color: var(--ink);
    display: flex; align-items: center; gap: 6px;
  }
  .brand-dot { width: 12px; height: 12px; border-radius: 50%; background: var(--ink); flex: none; }
  .brand-divider { width: 1px; height: 82px; background: #cbb99e; margin: 0 22px 0 8px; }
  .brand-org { font-size: 21px; color: var(--accent-orange); line-height: 1.1; }
  .brand-address { font-size: 15px; line-height: 1.3; margin-top: 3px; }

  .contact-line { position: absolute; left: 0; top: 1079px; width: 900px; text-align: center; font-size: 15px; word-spacing: 1px; }
  .contact-line span + span { margin-left: 24px; }
  .web-line { position: absolute; left: 0; top: 1099px; width: 900px; text-align: center; font-size: 15px; }
</style>
</head>
<body>
  <main class="menu-cover">
    <div class="cover-photo" role="img" aria-label="Photo of fresh red apples piled in a woven wicker basket"></div>

    <svg class="torn-edge top" viewBox="0 0 900 80" preserveAspectRatio="none" aria-hidden="true">
      <path d="M0 36 L40 32 L80 38 L120 34 L170 42 L210 40 L260 30 L300 18 L350 12 L400 14 L450 10 L500 14 L560 8 L610 10 L660 12 L700 20 L740 30 L790 26 L840 30 L900 28 L900 80 L0 80 Z" fill="var(--cream)" stroke="var(--paper-white)" stroke-width="5"/>
    </svg>

    <svg class="torn-edge bottom" viewBox="0 0 900 80" preserveAspectRatio="none" aria-hidden="true">
      <path d="M0 40 L50 34 L100 30 L150 26 L200 24 L240 34 L300 30 L360 34 L420 30 L480 24 L540 18 L580 12 L620 20 L680 24 L740 20 L800 26 L850 24 L900 26 L900 80 L0 80 Z" fill="var(--footer-beige)" stroke="var(--paper-white)" stroke-width="5"/>
    </svg>
    <div class="cover-footer"></div>

    <div class="title-block">
      <span class="title-script">Catering</span>
      <div class="title-serif-row">
        <span class="dot-rule"></span>
        <span class="title-serif">Menu</span>
        <span class="dot-rule"></span>
      </div>
    </div>

    <p class="audience">Conference Groups | Harvest Hall</p>
    <p class="pricing-note">Catering Menu pricing effective January 1, 2019</p>

    <div class="brand-row">
      <div class="brand-name-mark"><span class="brand-dot"></span>Maple Ridge Inn</div>
      <span class="brand-divider"></span>
      <div class="brand-details">
        <p class="brand-org">Maple Ridge Inn Conference Resort &amp; Spa</p>
        <p class="brand-address">Exit 7, Highway 104, 48 Valley View Road North,<br>Brookfield, Nova Scotia, B0N 1K3</p>
      </div>
    </div>

    <p class="contact-line"><span>T: (902) 555 0148</span><span>TF: 1 800 555 0192</span><span>F: (902) 555 0163</span></p>
    <p class="web-line">www.mapleridgeinn.com</p>
  </main>
</body>
</html>
```